Super elegant, crisp & clean Business card design required

We recently upgraded our branding - which is on our website - talvendoraphoto.com

I would like a simple, yet elegant, clean business card design please.

The font of my logo is Cinzel - and because of the natural colour - it's best to have this on a black background.

I would like to have the back of the business card - with simply my logo.

PLEASE DO NOT SUBMIT A COMPLICATED / UNCLEAN DESIGN

Industry/Entity Type

Business

Contact Information for Business Card

Talven Doroshko Photography

Font styles to use
Other font styles liked:
• Cinzel

Requirements
Must have
• A backpage with nothing but my logo
• Simple design - stands out
Should not have
• Colour that dont align with my logo
• Over complicated '/ non symmetrical design

```html
<!DOCTYPE html>
<html lang="en">
<head>
<meta charset="utf-8">
<title>Talven Doroshko Photography – Business Card</title>
<link rel="stylesheet" href="https://fonts.googleapis.com/css2?family=Cinzel:wght@400&family=Questrial&display=swap">
<style>
  :root {
    --backdrop: #1b1b1b;
    --taupe: #857660;
    --paper: #ffffff;
    --ink-light: #ffffff;
  }
  * { margin: 0; padding: 0; box-sizing: border-box; }
  html, body { width: 1200px; height: 741px; overflow: hidden; }
  body { background: var(--backdrop); position: relative; font-family: "Questrial", sans-serif; }

  .card { position: absolute; top: 229px; width: 494px; height: 282px; overflow: hidden; }

  /* Front */
  .card--front { left: 98px; background: var(--taupe); }
  .brand { position: absolute; left: 0; right: 0; text-align: center; font-family: "Cinzel", serif; }
  .brand__dot { position: absolute; left: 50%; transform: translateX(-50%); border-radius: 50%; border: 1.5px solid currentColor; }
  .brand__name { position: absolute; left: 0; right: 0; white-space: nowrap; text-transform: uppercase; }
  .brand__tag { position: absolute; left: 0; right: 0; text-transform: uppercase; }

  .card--front .brand { color: var(--ink-light); top: 0; height: 100%; }
  .card--front .brand__dot { top: 88px; width: 58px; height: 58px; }
  .card--front .brand__name { top: 170px; font-size: 19px; letter-spacing: 0.5px; }
  .card--front .brand__tag { top: 197px; font-size: 9px; letter-spacing: 7.5px; padding-left: 7px; }

  /* Back */
  .card--back { left: 608px; background: var(--taupe); }
  .back__logo-panel { position: absolute; left: 0; top: 0; width: 240px; height: 100%; background: var(--paper); }
  .back__rule { position: absolute; left: 242px; top: 0; width: 2px; height: 100%; background: var(--paper); }
  .card--back .brand { color: var(--taupe); top: 0; height: 100%; }
  .card--back .brand__dot { top: 95px; width: 50px; height: 50px; }
  .card--back .brand__name { top: 167px; font-size: 16px; }
  .card--back .brand__tag { top: 190px; font-size: 8px; letter-spacing: 6px; padding-left: 6px; }

  .holder { position: absolute; left: 264px; top: 56px; color: var(--ink-light); }
  .holder__name { font-family: "Cinzel", serif; font-size: 20px; line-height: 1; }
  .holder__title { font-size: 13px; margin-top: 2px; }

  .contacts { position: absolute; left: 264px; top: 172px; list-style: none; color: var(--ink-light); font-size: 13px; }
  .contacts li { display: flex; align-items: center; height: 17.5px; }
  .contacts svg { width: 13px; height: 13px; margin-right: 5px; flex: none; }
</style>
</head>
<body>
  <section class="card card--front" aria-label="Card front">
    <div class="brand">
      <span class="brand__dot"></span>
      <span class="brand__name">Talven Doroshko</span>
      <span class="brand__tag">Photography</span>
    </div>
  </section>

  <section class="card card--back" aria-label="Card back">
    <div class="back__logo-panel">
      <div class="brand">
        <span class="brand__dot"></span>
        <span class="brand__name">Talven Doroshko</span>
        <span class="brand__tag">Photography</span>
      </div>
    </div>
    <div class="back__rule"></div>

    <div class="holder">
      <p class="holder__name">ORIN VALE</p>
      <p class="holder__title">Chief Executive Officer</p>
    </div>

    <ul class="contacts">
      <li>
        <svg viewBox="0 0 13 13" aria-hidden="true"><rect width="13" height="13" rx="1.5" fill="#fff"/><path d="M3 4.5c0-1 1-1.5 3.5-1.5S10 3.5 10 4.5v.8H8.3v-.8H4.7v.8H3zM4 6h5l1 3.5H3z" fill="#857660"/></svg>
        <span>44 7700 900318</span>
      </li>
      <li>
        <svg viewBox="0 0 13 13" aria-hidden="true"><rect width="13" height="13" rx="1.5" fill="#fff"/><rect x="2.5" y="3.5" width="8" height="6" fill="none" stroke="#857660" stroke-width="1"/><path d="M2.5 3.5l4 3.3 4-3.3" fill="none" stroke="#857660" stroke-width="1"/></svg>
        <span>td.photography@inboxmail.com</span>
      </li>
      <li>
        <svg viewBox="0 0 13 13" aria-hidden="true"><rect width="13" height="13" rx="1.5" fill="#fff"/><circle cx="6.5" cy="6.5" r="4" fill="none" stroke="#857660" stroke-width="1"/><path d="M2.5 6.5h8M6.5 2.5c-1.6 2.4-1.6 5.6 0 8M6.5 2.5c1.6 2.4 1.6 5.6 0 8" fill="none" stroke="#857660" stroke-width="0.8"/></svg>
        <span>www.talvendoraphoto.com</span>
      </li>
    </ul>
  </section>
</body>
</html>
```